Two Wine Labels, One Red One White

We are looking to create a brand image for our wines. There are two requirements by law that we need, however beyond that, the creativity comes from the designer. Required are:
On The Red Label, Alcohol 14.1White Label Alcohol 12.5, The Size, 750ML
SO One label for the red wine with alcohol at 14.1 in a 750 ML Bottle, and one Label for white with alcohol at 12.5 in a 750 ML bottle.

Hi All:
I have some more clarity to assist in the design work.
The Brand Name of the wine is Valquine for both the red and the white
The name should appear as Valquine with the Brackets around phonetical as seen here
[val-keen] Both the word and the phonetical spelling should appear.
and can be seen on lexiquarry.com The Brand Name text can be black
Label should be very light grey, I am trying to capture a Stone grey or texture from stone, although, NOT Marble.
The Red Label, The word "Red" should be in red
The White Label, The word "White" should be in White, all the original remaining elements remain as originally posted.

I look forward to hearing from you for any additional questions.
Updates

Just added a logo Not really seeing what we are trying to achieve, maybe using the logo in the design may assist

Target Market(s)

Wine Aficionados

Requirements
Must have
• Details described in Project Description above, these are required by law. The Name of the Brand will be posted shortly. For the moment if you take the project, just place red on one label and white on the other.
Nice to have
• These two wines are from California (USA), so the Sierra Nevada Mountains could be an inspiration, to outline of California or coast line, a vineyard (of course), a vine...We are in silicon valley, so there is a map of silicon valley with the Bay and ocean, something from a map could work, or let your creativity flow and not use any of these concepts.
Should not have
• I do not not care for decorative fonts, however all else is open

```html
<!DOCTYPE html>
<html lang="en">
<head>
<meta charset="utf-8">
<title>Valquine Wine Labels</title>
<link rel="stylesheet" href="https://fonts.googleapis.com/css2?family=Cinzel:wght@700&family=PT+Sans&display=swap">
<style>
  :root {
    --backdrop: #130004;
    --stone: #ecebe8;
    --stone-light: #f4f3f1;
    --stone-dark: #e2e0dc;
    --white: #ffffff;
    --ink: #111111;
    --red: #ed1c24;
    --gold: #f7d33f;
    --green-text: #2db37a;
  }
  html, body {
    margin: 0;
    padding: 0;
    width: 1200px;
    height: 900px;
    overflow: hidden;
    background: var(--backdrop);
  }
  .canvas {
    position: relative;
    width: 1200px;
    height: 900px;
  }
  .label {
    position: absolute;
    top: 130px;
    width: 458px;
    height: 640px;
    background:
      radial-gradient(ellipse at 70% 40%, var(--stone-light) 0%, var(--stone) 55%, var(--stone-dark) 100%);
    overflow: hidden;
  }
  .label--red { left: 107px; }
  .label--white { left: 635px; }
  .label__art {
    position: absolute;
    inset: 0;
    width: 458px;
    height: 640px;
  }
  .label__tag {
    position: absolute;
    left: 307px;
    top: 160px;
    width: 131px;
    height: 44px;
    color: var(--white);
    font: 400 35px/44px "PT Sans", sans-serif;
    text-align: center;
  }
  .label--red .label__tag { background: var(--red); }
  .label--white .label__tag { background: var(--gold); }
  .label__brand {
    position: absolute;
    right: 20px;
    top: 276px;
    margin: 0;
    color: var(--ink);
    font: 700 50px/56px "Cinzel", serif;
    letter-spacing: -0.5px;
    white-space: nowrap;
  }
  .label__phonetic {
    position: absolute;
    right: 28px;
    top: 334px;
    margin: 0;
    font: 400 28px/34px "PT Sans", sans-serif;
    white-space: nowrap;
  }
  .label--red .label__phonetic { color: var(--red); }
  .label--white .label__phonetic { color: var(--green-text); }
  .label__facts {
    position: absolute;
    right: 22px;
    top: 452px;
    margin: 0;
    color: var(--ink);
    font: 400 20px/31px "PT Sans", sans-serif;
    text-align: right;
  }
</style>
</head>
<body>
<main class="canvas">

  <section class="label label--red">
    <svg class="label__art" viewBox="0 0 458 640" role="img" aria-label="Abstract splash illustration of red grapes and yellow leaves framing the label">
      <defs>
        <linearGradient id="splash-red" x1="0" y1="0" x2="1" y2="1">
          <stop offset="0" stop-color="#ed1c24"/>
          <stop offset="0.45" stop-color="#f2702c"/>
          <stop offset="1" stop-color="#fce13a"/>
        </linearGradient>
      </defs>
      <path fill="url(#splash-red)" fill-rule="evenodd"
        d="M0 0H458V640H0Z M470 95 C330 80 160 90 110 150 C70 200 60 260 80 320 C60 390 75 460 120 500 C180 555 330 560 470 545 Z"/>
    </svg>
    <div class="label__tag">Red</div>
    <h1 class="label__brand">VALQUINE</h1>
    <p class="label__phonetic">[val-keen]</p>
    <p class="label__facts">Alcohol 14.1<br>750мл.</p>
  </section>

  <section class="label label--white">
    <svg class="label__art" viewBox="0 0 458 640" role="img" aria-label="Abstract splash illustration of green grapes and yellow leaves framing the label">
      <defs>
        <linearGradient id="splash-green" x1="0" y1="0" x2="1" y2="1">
          <stop offset="0" stop-color="#23b574"/>
          <stop offset="0.45" stop-color="#8cc84f"/>
          <stop offset="1" stop-color="#fce13a"/>
        </linearGradient>
      </defs>
      <path fill="url(#splash-green)" fill-rule="evenodd"
        d="M0 0H458V640H0Z M470 95 C330 80 160 90 110 150 C70 200 60 260 80 320 C60 390 75 460 120 500 C180 555 330 560 470 545 Z"/>
    </svg>
    <div class="label__tag">White</div>
    <h2 class="label__brand">VALQUINE</h2>
    <p class="label__phonetic">[val-keen]</p>
    <p class="label__facts">Alcohol 12.5<br>750мл.</p>
  </section>

</main>
</body>
</html>
```